Nonprofit needs table front banner

Bright Meridian is a disability advocacy organization in Indiana. We are requesting a graphic design for a table front banner 28 inches high and 72 inches long. The banner must incorporate Bright Meridian’s logo, and the logos of our two web projects, AidLantern and Plumvine. (See attached items.) We would also like the banner to incorporate our slogan, and the slogans of AidLantern and Plumvine:

• AidLantern slogan: “Searching for Accessible Support Should Never Feel Like Wandering Through a Maze. With AidLantern, the Right Path Lights Up.”

• Bright Meridian slogan: “Indiana’s Source for Disability News and Information”

• Plumvine slogan: “Where Workers with Disabilities and Inclusive Employers Connect!”

As Bright Meridian is the organization and AidLantern and Plumvine are our projects, we would like Bright Meridian’s logo and slogan to be in the middle, and slightly more prominent. Also, as we are a disability organization, the banner should be designed with basic accessibility in mind. This means large text in a clear font, with good contrast between the text and the background. The text should be in a sans serif font that is clear and easy to read, with no italics or script fonts. There should not be a "busy" picture or pattern behind the text.

Industry/Entity Type

Non-Profit

Font styles to use
Sans Serif

Requirements
Must have
• The banner must incorporate Bright Meridian’s logo, and the logos of our two web projects, AidLantern and Plumvine. (See attached items.) We would also like the banner to incorporate our slogan, and the slogans of AidLantern and Plumvine:
• • AidLantern slogan: “Searching for Accessible Support Should Never Feel Like Wandering Through a Maze. With AidLantern, the Right Path Lights Up.”
• • Bright Meridian slogan: “Indiana’s Source for Disability News and Information”
• • Plumvine slogan: “Where Workers with Disabilities and Inclusive Employers Connect!”
Nice to have
• As Bright Meridian is the organization and AidLantern and Plumvine are our projects, we would like Bright Meridian’s logo and slogan to be in the middle, and slightly more prominent.
Should not have
• No italics or script fonts. There should not be a "busy" picture or pattern behind the text.

```html
<!DOCTYPE html>
<html lang="en">
<head>
<meta charset="utf-8">
<title>Bright Meridian – Table Front Banner</title>
<link rel="stylesheet" href="https://fonts.googleapis.com/css2?family=Mulish:wght@400;600;700;800&display=swap">
<style>
  :root {
    --brand-blue: #2c52a0;
    --paper: #ffffff;
    --frame: #1a1a1a;
  }
  * { box-sizing: border-box; margin: 0; padding: 0; }
  html, body { width: 1200px; height: 466px; overflow: hidden; background: var(--paper); }
  .banner {
    position: relative;
    width: 1200px;
    height: 466px;
    background: var(--paper);
    font-family: "Mulish", "Helvetica Neue", Arial, sans-serif;
    overflow: hidden;
  }
  .banner__shapes { position: absolute; inset: 0; }

  .org {
    position: absolute;
    left: 240px;
    top: 38px;
    width: 720px;
    display: flex;
    flex-direction: column;
    align-items: center;
    text-align: center;
    color: var(--brand-blue);
  }
  .org__mark {
    display: flex;
    align-items: center;
    gap: 18px;
  }
  .org__dot {
    width: 60px; height: 60px;
    border-radius: 50%;
    background: var(--brand-blue);
    flex: none;
  }
  .org__name {
    font-size: 62px;
    line-height: 76px;
    font-weight: 800;
    letter-spacing: -0.5px;
    white-space: nowrap;
  }
  .org__slogan {
    margin-top: 16px;
    font-size: 40px;
    line-height: 50px;
    font-weight: 800;
  }

  .project {
    position: absolute;
    top: 330px;
    color: var(--paper);
  }
  .project--aid { left: 70px; width: 590px; }
  .project--plum { left: 720px; width: 360px; }
  .project__slogan {
    font-size: 20px;
    line-height: 26px;
    font-weight: 600;
  }
  .project__mark {
    display: flex;
    align-items: center;
    gap: 10px;
    margin-top: 12px;
  }
  .project__dot {
    width: 34px; height: 34px;
    border-radius: 50%;
    background: var(--paper);
    flex: none;
  }
  .project__name {
    font-size: 28px;
    line-height: 34px;
    font-weight: 700;
    color: var(--paper);
  }
</style>
</head>
<body>
<div class="banner">
  <svg class="banner__shapes" width="1200" height="466" viewBox="0 0 1200 466" aria-hidden="true">
    <path fill="var(--brand-blue)" d="M0 0 H232 C150 32 64 70 0 100 Z"/>
    <path fill="var(--brand-blue)" d="M0 128 C60 102 120 92 180 88 C110 110 50 150 0 186 Z"/>
    <path fill="var(--brand-blue)" d="M0 232 C40 208 80 192 112 184 C72 206 32 236 0 262 Z"/>
    <rect x="0" y="312" width="1200" height="154" fill="var(--brand-blue)"/>
    <path fill="var(--paper)" d="M1200 318 C1160 338 1122 354 1096 362 C1140 362 1176 350 1200 340 Z"/>
    <path fill="var(--paper)" d="M1200 372 C1150 390 1112 398 1090 402 C1140 405 1176 398 1200 392 Z"/>
    <path fill="var(--paper)" d="M1200 428 C1150 446 1080 456 1040 466 H1200 Z"/>
    <rect x="1" y="1" width="1198" height="464" fill="none" stroke="var(--frame)" stroke-width="2"/>
  </svg>

  <header class="org">
    <div class="org__mark">
      <span class="org__dot"></span>
      <span class="org__name">Bright Meridian</span>
    </div>
    <h1 class="org__slogan">Indiana’s Source for<br>Disability News and Information</h1>
  </header>

  <section class="project project--aid">
    <p class="project__slogan">Searching for Accessible Support Should Never Feel Like Wandering Through a Maze. With AidLantern, the Right Path Lights Up.</p>
    <div class="project__mark">
      <span class="project__dot"></span>
      <span class="project__name">AidLantern</span>
    </div>
  </section>

  <section class="project project--plum">
    <p class="project__slogan">Where Workers with Disabilities and Inclusive Employers Connect!</p>
    <div class="project__mark">
      <span class="project__dot"></span>
      <span class="project__name">Plumvine</span>
    </div>
  </section>
</div>
</body>
</html>
```